Home Loan Introducer needs logo/business cards

We need a simple but classy logo for business cards and flyers. The business is a home loan referral business that is called an Introducer. The business name is "The Harborline".
I was thinking very simple and straight to the point on the front with "Home Loans" the only thing on the front with a nice background colour/s.
Then on the back, "The Harborline"
and "Quality Customer Service"
and "Email, text or call welcome"
and then my name, email address and phone number.
Updates
Thank you for all the designs :-)
Target Market(s)
Home buyers.
Home owners.
Investors.
Industry/Entity Type
Loan
Look and feel

```html
<!DOCTYPE html>
<html lang="en">
<head>
<meta charset="UTF-8">
<title>The Harborline – Business Cards</title>
<link rel="stylesheet" href="https://fonts.googleapis.com/css2?family=Play:wght@400;700&display=swap">
<style>
  :root {
    --bg: #efeae4;
    --card-dark: #1e1e1e;
    --accent-yellow: #fbb034;
    --accent-blue: #1a6fc4;
    --text-light: #ffffff;
    --text-dark: #1e1e1e;
  }
  * { margin: 0; padding: 0; box-sizing: border-box; }
  html, body {
    width: 1200px; height: 750px; overflow: hidden;
    background: var(--bg);
    font-family: "Play", sans-serif;
  }
  .canvas {
    position: relative; width: 1200px; height: 750px;
  }
  .card {
    position: absolute; top: 220px;
    width: 520px; height: 310px;
    background: var(--card-dark);
    overflow: hidden;
  }
  .card--contact { left: 50px; }
  .card--front { left: 630px; }

  /* Contact side */
  .contact-base {
    position: absolute; left: 0; right: 0; bottom: 0; height: 112px;
    background: var(--accent-yellow);
  }
  .brand {
    position: absolute; top: 26px; left: 0; right: 0;
    display: flex; flex-direction: column; align-items: center; gap: 10px;
  }
  .brand-dot {
    width: 54px; height: 54px; border-radius: 50%;
    background: var(--accent-blue);
  }
  .brand-name {
    background: var(--accent-yellow);
    color: var(--text-light);
    font-weight: 700; font-size: 22px; letter-spacing: 0.5px;
    padding: 3px 18px; border-radius: 5px;
    text-transform: uppercase;
  }
  .perks {
    position: absolute; top: 142px; left: 168px;
    list-style: none; color: var(--accent-blue); font-size: 15px; line-height: 20px;
  }
  .perks li { display: flex; align-items: center; gap: 4px; }
  .perks svg { width: 14px; height: 14px; flex: none; }
  .person {
    position: absolute; top: 212px; left: 0; right: 0; text-align: center;
  }
  .person-name {
    color: var(--text-dark); font-size: 20px; font-weight: 700;
    display: inline-block; padding: 0 14px 2px;
    border-bottom: 2px solid var(--text-light);
  }
  .person-details {
    margin-top: 4px; font-size: 10px; line-height: 13px; color: var(--text-light);
  }
  .person-details span { color: var(--accent-blue); }

  /* Front side */
  .headline-band {
    position: absolute; left: 0; right: 0; top: 108px; height: 102px;
    background: var(--accent-yellow);
    border: 5px solid var(--text-light); border-left: none; border-right: none;
    display: flex; align-items: center; justify-content: center; gap: 22px;
    font-weight: 700; font-size: 64px; letter-spacing: 1px;
  }
  .headline-home { color: var(--text-light); }
  .headline-loan { color: var(--accent-blue); }
</style>
</head>
<body>
<main class="canvas">
  <section class="card card--contact" aria-label="Contact side">
    <div class="contact-base"></div>
    <div class="brand">
      <div class="brand-dot"></div>
      <div class="brand-name">The Harborline</div>
    </div>
    <ul class="perks">
      <li><svg viewBox="0 0 14 14"><path d="M2 7 L5.5 11 L12 2" fill="none" stroke="#fff" stroke-width="2.4" stroke-linecap="round"/></svg>Quality Customer Service</li>
      <li><svg viewBox="0 0 14 14"><path d="M2 7 L5.5 11 L12 2" fill="none" stroke="#fff" stroke-width="2.4" stroke-linecap="round"/></svg>Email, text or call welcome</li>
    </ul>
    <div class="person">
      <div class="person-name">Owen Hale</div>
      <div class="person-details">
        Phone: <span>+6391045876</span><br>
        Email: <span>owen@harborline.net</span>
      </div>
    </div>
  </section>

  <section class="card card--front" aria-label="Front side">
    <div class="headline-band">
      <span class="headline-home">HOME</span>
      <span class="headline-loan">LOAN</span>
    </div>
  </section>
</main>
</body>
</html>
```